Book Cover Project

This is a printed journal front and back cover design. We like the current design, but it feels a little too flat / too simple.

NOTE: we are not looking for a total makeover, just a finishing / polishing of this cover.

Here is our other book cover: https://www.shelvora-books.example/Quiet-Studio-Ledger-Fine-Morning/dp/7093268415/ref=tmm_hrd_swatch_0?_encoding=UTF8&qid=&sr=
it's purple and yellow (mostly purple)
this one is yellow and we're thinking to add a purple bar at the bottom

Specs: 6 in x 9 in full bleed for print

```html
<!DOCTYPE html>
<html lang="en">
<head>
<meta charset="utf-8">
<title>Silent Strides – Journal Cover</title>
<link rel="stylesheet" href="https://fonts.googleapis.com/css2?family=Anton&display=swap">
<style>
  :root {
    --cover-yellow: #ffd500;
    --ink: #141414;
    --band-purple: #5a4fa6;
    --runner-tone: #ecc600;
  }
  html, body {
    margin: 0;
    padding: 0;
    width: 805px;
    height: 1200px;
    overflow: hidden;
    background: var(--cover-yellow);
  }
  .cover {
    position: relative;
    width: 805px;
    height: 1200px;
    background: var(--cover-yellow);
    font-family: "Anton", "Impact", sans-serif;
    color: var(--ink);
  }
  .title-art {
    position: absolute;
    left: 0;
    top: 0;
    width: 805px;
    height: 920px;
  }
  .title-word {
    font-family: "Anton", "Impact", sans-serif;
    fill: var(--ink);
  }
  .tagline {
    font-family: "Anton", "Impact", sans-serif;
    fill: var(--ink);
    font-size: 32px;
  }
  .runner-figure {
    fill: var(--runner-tone);
  }
  .author-band {
    position: absolute;
    left: 0;
    bottom: 0;
    width: 805px;
    height: 79px;
    background: var(--band-purple);
    display: flex;
    align-items: center;
    justify-content: center;
  }
  .author-name {
    margin: 0;
    font-family: "Anton", "Impact", sans-serif;
    font-weight: 400;
    font-size: 34px;
    letter-spacing: 5px;
    color: var(--cover-yellow);
    line-height: 1;
  }
</style>
</head>
<body>
  <main class="cover">
    <svg class="title-art" viewBox="0 0 805 920" width="805" height="920" aria-labelledby="book-title">
      <title id="book-title">Silent Strides</title>
      <g class="runner-figure" role="img" aria-label="Single-line drawing of a runner standing in for the letter I">
        <rect x="196" y="201" width="148" height="261" rx="40"/>
      </g>
      <text class="title-word" x="102" y="462" font-size="263" textLength="84" lengthAdjust="spacingAndGlyphs">S</text>
      <text class="title-word" x="354" y="462" font-size="263" textLength="376" lengthAdjust="spacingAndGlyphs">LENT</text>
      <text class="title-word" x="102" y="757" font-size="281" textLength="628" lengthAdjust="spacingAndGlyphs">STRIDES</text>
      <text class="tagline" x="215" y="885" textLength="380" lengthAdjust="spacing">PACE - REFLECT - GROW</text>
    </svg>

    <footer class="author-band">
      <p class="author-name">MARCUS HOLLOWAY</p>
    </footer>
  </main>
</body>
</html>
```